Calvanto Group Real Estate Company business cards

New business card design, we are generally happy with the basic layout of the existing front of business card, (feel free to change) but require a head shot photo on the back side.

http://www.calvanto.com.au/

Attached logos, and existing business card

------------------------------

Target Market(s)

Real estate

Industry/Entity Type

Real Estate

Contact Information for Business Card

Standard size double sided

Font styles to use
Other font styles liked:
• Futura

Requirements
Must have
• Photo head shot on the back side
Nice to have
• yes
Should not have
• No

```html
<!DOCTYPE html>
<html lang="en">
<head>
<meta charset="utf-8">
<title>Calvanto Group – Business Cards</title>
<link rel="stylesheet" href="https://fonts.googleapis.com/css2?family=Arimo:wght@400;700&display=swap">
<style>
  :root {
    --bg: #e8e5e0;
    --purple: #3f1f8a;
    --purple-ink: #3b3358;
    --orange: #e8961e;
    --ink: #111111;
    --paper: #ffffff;
    --photo-light: #d9d6e2;
    --photo-mid: #8e88a6;
    --portrait-light: #eceeef;
    --portrait-dark: #2f3646;
  }
  * { box-sizing: border-box; margin: 0; padding: 0; }
  html, body { width: 1200px; height: 864px; overflow: hidden; }
  body {
    background: var(--bg);
    display: flex;
    align-items: center;
    justify-content: center;
    gap: 40px;
    font-family: "Arimo", Arial, sans-serif;
  }
  .card {
    position: relative;
    width: 560px;
    height: 342px;
    background: var(--paper);
    box-shadow: 0 6px 18px rgba(0,0,0,0.18);
    overflow: hidden;
  }
  .card-art { position: absolute; inset: 0; width: 100%; height: 100%; }

  .brand-name {
    position: absolute;
    font-family: "Arimo", Arial, sans-serif;
    font-weight: 700;
    font-size: 34px;
    line-height: 1;
    white-space: nowrap;
  }
  .front .brand-name { color: var(--purple-ink); top: 66px; right: 30px; }
  .back { background: var(--purple); }
  .back .brand-name { color: var(--paper); left: 42px; bottom: 84px; }

  .contact {
    position: absolute;
    top: 150px;
    left: 250px;
    width: 280px;
    text-align: center;
    color: var(--ink);
    font-size: 15px;
    line-height: 1.3;
  }
  .contact-name { color: var(--orange); font-weight: 700; font-size: 25px; letter-spacing: 0.5px; }
  .contact-role { font-size: 15px; margin-bottom: 12px; }
  .contact-rule { border: 0; border-top: 1.5px solid var(--ink); margin: 6px 0 8px; }
  .contact-abn { font-size: 16px; }
</style>
</head>
<body>

  <section class="card front" aria-label="Business card front">
    <svg class="card-art" viewBox="0 0 560 342">
      <defs>
        <linearGradient id="lock-photo" x1="0" y1="0" x2="1" y2="1">
          <stop offset="0" stop-color="var(--photo-mid)"/>
          <stop offset="0.55" stop-color="var(--photo-light)"/>
          <stop offset="1" stop-color="var(--photo-mid)"/>
        </linearGradient>
      </defs>
      <path role="img" aria-label="Photo of a gold key inserted in a door lock"
            fill="url(#lock-photo)"
            d="M0 20 C90 30 180 20 250 60 C200 120 190 200 215 260 C228 295 240 320 248 342 H0 Z"/>
    </svg>

    <p class="brand-name">Calvanto Group</p>

    <div class="contact">
      <p class="contact-name">Daniel Tran</p>
      <p class="contact-role">Director</p>
      <p>0400 555 218</p>
      <p>www.calvanto.com.au</p>
      <p>daniel.tran@calvanto.com.au</p>
      <hr class="contact-rule">
      <p class="contact-abn">ABN: 12 345 678 901</p>
    </div>
  </section>

  <section class="card back" aria-label="Business card back">
    <svg class="card-art" viewBox="0 0 560 342">
      <defs>
        <linearGradient id="portrait" x1="0" y1="0" x2="0" y2="1">
          <stop offset="0" stop-color="var(--portrait-light)"/>
          <stop offset="0.55" stop-color="var(--portrait-light)"/>
          <stop offset="1" stop-color="var(--portrait-dark)"/>
        </linearGradient>
      </defs>
      <path role="img" aria-label="Head shot photo of the director in a suit and tie"
            fill="url(#portrait)" stroke="var(--orange)" stroke-width="3"
            d="M400 0 H560 V342 H480 C470 300 440 270 390 250 C360 240 345 235 338 228 C346 220 340 212 342 205 C350 190 372 180 378 150 C382 110 372 70 385 40 C390 25 396 12 400 0 Z"/>
    </svg>

    <p class="brand-name">Calvanto Group</p>
  </section>

</body>
</html>
```